Belmont Ridge Business Card Design Project

We have recently rebranded and would like to design new business cards that incorporate the corporate logo - double sided cards with corporate logo on one side and contact details on the other

Target Market(s)

Sophisticated and high net worth investors and finance industry professionals

Industry/Entity Type

Funds Management

Contact Information for Business Card

The card should prominently feature the company name and logo. Other details will be standard contact details for each staff member - name, address, phone, email, website

Colors
0054AA
0677BA
7BADD7
CADEEF
E8F1F8

Requirements
Must have
• Double-sided design with one side prominently featuring the corporate logo and the other side with all standard contact details

```html
<!DOCTYPE html>
<html lang="en">
<head>
<meta charset="utf-8">
<title>Belmont Ridge — Business Cards</title>
<link rel="stylesheet" href="https://fonts.googleapis.com/css2?family=Lato:wght@400;700&display=swap">
<style>
  :root {
    --navy: #21467a;
    --paper: #ffffff;
    --ink: #4a4a4a;
    --backdrop: #737373;
  }
  * { margin: 0; padding: 0; box-sizing: border-box; }
  html, body {
    width: 1200px; height: 1200px; overflow: hidden;
    background: var(--backdrop);
    font-family: "Lato", Arial, sans-serif;
  }
  .card {
    position: absolute; left: 281px;
    width: 638px; height: 365px;
    border-radius: 24px; overflow: hidden;
  }
  .card--front { top: 195px; background: var(--paper); }
  .card--back { top: 639px; background: var(--navy); }

  .card__band {
    position: absolute; left: 0; bottom: 0;
    width: 100%; height: 15px;
  }
  .card--front .card__band { background: var(--navy); }
  .card--back .card__band { background: var(--paper); }
  .card__band svg { position: absolute; left: 0; top: 0; }

  .brand-name {
    position: absolute; right: 43px; top: 70px;
    font-weight: 700; font-size: 32px; color: var(--navy);
    letter-spacing: 0.5px;
  }

  .holder { position: absolute; left: 42px; top: 182px; }
  .holder__name {
    font-weight: 700; font-size: 30px; line-height: 30px;
    color: var(--navy); letter-spacing: 0.3px;
  }
  .holder__title { font-size: 16px; color: var(--ink); margin-top: 3px; }

  .divider {
    position: absolute; left: 43px; top: 243px;
    width: 552px; height: 2px; background: var(--navy);
  }

  .contacts { position: absolute; left: 43px; top: 260px; list-style: none; }
  .contacts li {
    display: flex; align-items: center; height: 22px;
    font-size: 14px; color: var(--ink); letter-spacing: 0.9px;
  }
  .contacts svg { width: 11px; height: 11px; margin-right: 12px; fill: var(--navy); }

  .location {
    position: absolute; right: 42px; top: 262px;
    text-align: right; font-size: 14px; line-height: 20px;
    color: var(--ink); letter-spacing: 0.9px;
  }
  .location .web { color: var(--navy); margin-top: 1px; }
  .location .web strong { font-weight: 700; }

  .back-name {
    position: absolute; left: 0; right: 0; top: 136px;
    text-align: center; font-weight: 700; font-size: 58px;
    color: var(--paper); letter-spacing: 1px;
  }
</style>
</head>
<body>

<section class="card card--front">
  <div class="brand-name">Belmont Ridge</div>

  <div class="holder">
    <div class="holder__name">DANIEL HART</div>
    <div class="holder__title">Founder &amp; CEO</div>
  </div>

  <div class="divider"></div>

  <ul class="contacts">
    <li>
      <svg viewBox="0 0 12 12"><path d="M2.5 0.5 L4.5 0.5 L5.2 3.3 L3.8 4.3 C4.5 6 6 7.5 7.7 8.2 L8.7 6.8 L11.5 7.5 L11.5 9.5 C11.5 10.8 10.6 11.5 9.5 11.5 C4.5 11 1 7.5 0.5 2.5 C0.5 1.4 1.2 0.5 2.5 0.5 Z"/></svg>
      (555) 014-2736
    </li>
    <li>
      <svg viewBox="0 0 12 12"><path d="M3 0 H9 A1 1 0 0 1 10 1 V11 A1 1 0 0 1 9 12 H3 A1 1 0 0 1 2 11 V1 A1 1 0 0 1 3 0 Z M3.5 1.5 V9.5 H8.5 V1.5 Z M6 10 A0.7 0.7 0 1 0 6 11.4 A0.7 0.7 0 1 0 6 10 Z"/></svg>
      (555) 014-2736
    </li>
    <li>
      <svg viewBox="0 0 12 12"><path d="M0 2 H12 V3 L6 6.6 L0 3 Z M0 4.2 L6 7.8 L12 4.2 V10 H0 Z"/></svg>
      info@belmontridge.com
    </li>
  </ul>

  <div class="location">
    <div>4820 Calder Lane</div>
    <div>Westfield, CT 06412</div>
    <div class="web">www.<strong>BelmontRidge</strong>.com</div>
  </div>

  <div class="card__band">
    <svg width="638" height="15" viewBox="0 0 638 15">
      <path d="M437 16 Q445 3 466 0" fill="none" stroke="#ffffff" stroke-width="3"/>
    </svg>
  </div>
</section>

<section class="card card--back">
  <div class="back-name">Belmont Ridge</div>
  <div class="card__band">
    <svg width="638" height="15" viewBox="0 0 638 15">
      <path d="M437 16 Q445 3 466 0" fill="none" stroke="#21467a" stroke-width="3"/>
    </svg>
  </div>
</section>

</body>
</html>
```